Website for a service provided by a Canadian Immigration Company

Design and Code a website for a Canadian immigration company which provides service to clients all across the world. the website should be very Canadian centric and have 4-5 pages. Basic, classy modern. I have the logo s already designed. Please contact me and I can send you some more details. It's basically a service which is provided to clients who are below 17 and need a guardian in canada to sign their documents that they will be looked after them. It's called custodianship. You can google the term and you will understand what it means
Updates

didn't realize it was just a day

Target Market(s)

17-55

Industry/Entity Type

Immigration

Coding

Coded - Design and coding required

Number of Pages Required

5+ page

Font styles to use
Sans Serif

Colors
EE7325
F08F49
F5BC92
FAE3D3
FDF4ED
EB3D1F
EC4F4E
F09395
F8D3D4
FCEDEE

Requirements
Must have
• Pages with some graphics, some small animations like clients served, projects completed

```html
<!DOCTYPE html>
<html lang="en">
<head>
<meta charset="utf-8">
<title>guardnest.ca — Custodianship for International Students</title>
<link href="https://fonts.googleapis.com/css2?family=Rubik:wght@500;700&family=Roboto:wght@400;500;700&display=swap" rel="stylesheet">
<style>
:root{
  --red:#e8232b;
  --red-deep:#c9161d;
  --black:#0b0b0b;
  --ink:#111;
  --grey:#6d6d6d;
  --light:#f3f3f3;
  --white:#fff;
}
*{margin:0;padding:0;box-sizing:border-box}
html,body{width:1200px;height:3556px;overflow:hidden;background:var(--white)}
body{font-family:"Roboto",sans-serif;color:var(--ink);position:relative}
.page{position:relative;width:1200px;height:3556px;overflow:hidden}
.abs{position:absolute}
h1,h2,h3{font-family:"Rubik",sans-serif}

/* header */
.site-header{left:0;top:0;width:1200px;height:137px;background:var(--black)}
.brand-wedge{left:0;top:0}
.brand{left:112px;top:46px;display:flex;align-items:center;gap:14px;color:var(--white);font:700 34px "Roboto",sans-serif;letter-spacing:-.5px}
.brand .dot{width:34px;height:34px;border-radius:50%;background:var(--white)}
.topbar{right:112px;top:32px;display:flex;align-items:center;gap:22px;color:var(--white);font-size:17px}
.topbar .call small{color:var(--red);font-size:11px;margin-right:6px}
.social-sq{width:14px;height:14px;border:2px solid var(--white);border-radius:3px}
.main-nav{right:112px;top:83px;display:flex;gap:40px}
.main-nav a{color:var(--white);font:700 15px "Roboto",sans-serif;text-decoration:none}

/* hero */
.hero-photo{left:0;top:137px;width:1200px;height:700px;background:linear-gradient(180deg,#7b8a99 0%,#d89a52 28%,#b76b32 42%,#3b2a22 58%,#5d4a40 75%,#2d2623 100%)}
.hero-text{left:0;top:342px;width:1200px;text-align:center;color:var(--white)}
.hero-text .pre{font:500 21px "Rubik",sans-serif}
.hero-text h1{font-size:46px;font-weight:700;margin-top:2px;letter-spacing:.5px}
.hero-text p{font-size:18px;line-height:28px;margin-top:14px}
.btn{display:inline-flex;align-items:center;gap:8px;background:var(--red);color:var(--white);font:700 14px "Roboto",sans-serif;text-decoration:none;text-transform:uppercase}
.btn .arr{width:13px;height:13px;border-radius:50%;background:var(--white);position:relative}
.btn .arr::after{content:"";position:absolute;left:4px;top:3.5px;border-left:5px solid var(--red);border-top:3px solid transparent;border-bottom:3px solid transparent}
.hero-text .btn{margin-top:22px;padding:15px 20px}
.hero-curve{left:0;top:560px}
.hero-badge{left:549px;top:729px;width:102px;height:102px;border-radius:50%;background:var(--white);box-shadow:0 6px 14px rgba(0,0,0,.18);display:flex;align-items:center;justify-content:center}
.hero-badge span{width:26px;height:26px;border-radius:50%;background:var(--red)}

/* about */
.about-title{left:112px;top:965px;font-size:37px;display:flex;align-items:center;gap:26px}
.about-title::after{content:"";width:76px;height:3px;background:var(--red)}
.about-copy{left:112px;top:1036px;width:438px;color:var(--grey);font-size:14.5px;line-height:26px;text-align:justify}
.about-btn{left:112px;top:1229px;padding:16px 24px}
.about-frame{left:921px;top:905px;width:167px;height:166px;border:2px solid var(--red)}
.about-dots{left:590px;top:1230px;width:122px;height:120px;background-image:radial-gradient(#c9c9c9 1.6px,transparent 1.7px);background-size:12.5px 12.5px}
.about-photo{left:628px;top:942px;width:424px;height:370px;border:4px solid var(--white);box-shadow:0 4px 18px rgba(0,0,0,.2);background:linear-gradient(135deg,#e9e2d6,#b99b7c 45%,#5e6e86 80%,#3b4555)}

/* services */
.services{left:0;top:1450px;width:1200px;height:622px;background:radial-gradient(ellipse at 50% 45%,#2a2624 0%,#141212 55%,#0b0a0a 100%)}
.section-title{width:1200px;left:0;text-align:center;font-size:40px;font-weight:700}
.section-title::after{content:"";display:block;width:76px;height:3px;background:var(--red);margin:6px auto 0}
.services .section-title{color:var(--white);top:64px}
.svc-map{left:0;top:0}
.svc-text{color:var(--white);font-size:15.5px;line-height:26px;width:220px}
.svc-text.l{text-align:right;left:82px}
.svc-text.r{left:898px}
.svc-hub{left:482px;top:241px;width:236px;height:236px;border-radius:50%;background:var(--white);display:flex;align-items:center;justify-content:center;color:var(--red);font:700 30px "Roboto",sans-serif}

/* articles */
.articles .section-title{top:2168px}
.art-card{width:274px;height:377px}
.art-card .img{width:274px;height:217px}
.art-card .box{position:absolute;left:12px;top:196px;width:250px;height:181px;background:var(--white);box-shadow:0 4px 14px rgba(0,0,0,.12);text-align:center;padding:26px 16px 0}
.art-card h3,.art-item h3{font:500 15px/26px "Roboto",sans-serif;text-transform:uppercase;color:var(--ink)}
.art-card p{color:var(--grey);font-size:14px;line-height:22px;margin-top:10px}
.art-item{left:685px;width:403px;height:119px}
.art-item .img{position:absolute;left:0;top:0;width:137px;height:119px}
.art-item .txt{position:absolute;left:160px;top:8px;width:245px}
.art-item p{color:var(--grey);font-size:14px;line-height:22px;margin-top:12px}

/* contact */
.contact{left:0;top:2751px;width:1200px;height:805px;background:linear-gradient(120deg,#e8232b 0%,#d81c24 50%,#e5242c 100%)}
.contact .section-title{color:var(--white);top:60px}
.contact .section-title::after{background:var(--white)}
.field{background:var(--white);color:#777;font-size:14px;padding:0 17px;display:flex;align-items:center}
.field.msg{align-items:flex-start;padding-top:22px}
.send{left:518px;top:320px;width:163px;height:49px;background:var(--black);color:var(--white);font:700 15px "Roboto",sans-serif;display:flex;align-items:center;justify-content:center}

/* footer */
.footer-shape{left:0;top:3170px}
.footer-brand{left:0;top:3300px;width:1200px;display:flex;justify-content:center;align-items:center;gap:14px;color:var(--white);font:700 34px "Roboto",sans-serif}
.footer-brand .dot{width:34px;height:34px;border-radius:50%;background:var(--red)}
.footer-nav{left:0;top:3368px;width:1200px;display:flex;justify-content:center;gap:26px;color:var(--white);font:700 16px "Roboto",sans-serif}
.footer-nav .sep{font-weight:400}
.footer-contact{left:0;top:3409px;width:1200px;display:flex;justify-content:center;gap:22px;color:var(--white);font-size:15px;align-items:center}
.footer-contact .ic{display:inline-block;vertical-align:middle;margin-right:10px}
.footer-social{left:0;top:3448px;width:1200px;display:flex;justify-content:center;gap:6px}
.footer-social span{width:36px;height:36px;border-radius:50%;background:var(--white)}
.footer-social span.on{background:var(--red)}
.footer-rule{left:112px;top:3506px;width:976px;height:1px;background:#444}
.copyright{left:0;top:3526px;width:1200px;text-align:center;color:var(--white);font-size:12px}
</style>
</head>
<body>
<div class="page">

  <!-- header -->
  <header class="site-header abs">
    <svg class="brand-wedge abs" width="530" height="137" viewBox="0 0 530 137"><polygon points="0,0 525,0 440,137 0,137" fill="#e8232b"/></svg>
    <div class="brand abs"><span class="dot"></span>guardnest.ca</div>
    <div class="topbar abs">
      <span class="call"><small>Call Us Today!</small>+1 (555) 010 2040</span>
      <span class="social-sq"></span><span class="social-sq"></span><span class="social-sq"></span>
    </div>
    <nav class="main-nav abs">
      <a href="#">HOME</a><a href="#">ABOUT US</a><a href="#">SERVICES</a><a href="#">RESOURCES</a><a href="#">CONTACT US</a>
    </nav>
  </header>

  <!-- hero -->
  <section class="hero">
    <div class="hero-photo abs" role="img" aria-label="City skyline with a tall tower at sunset over the lake"></div>
    <div class="hero-text abs">
      <div class="pre">WELCOME TO</div>
      <h1>GUARDNEST</h1>
      <p>We provide the required signed and notarized custodian declaration<br>along with formal supervision service</p>
      <a class="btn" href="#">Get Started <span class="arr"></span></a>
    </div>
    <svg class="hero-curve abs" width="1200" height="280" viewBox="0 0 1200 280">
      <path d="M0,30 Q600,400 1200,30 L1200,280 L0,280 Z" fill="#e8232b"/>
      <path d="M0,70 Q600,405 1200,52 L1200,280 L0,280 Z" fill="#fff"/>
    </svg>
    <div class="hero-badge abs"><span></span></div>
  </section>

  <!-- about -->
  <section class="about">
    <h2 class="about-title abs">ABOUT US</h2>
    <p class="about-copy abs">We provide the required signed and notarized custodian declaration along with formal supervision service upon the student's arrival in Canada. According to the Federal Student Permit Office (FSPO), minor students can be accepted at a university or college, but they cannot obtain a study permit without the required signed and notarized custodianship form.</p>
    <a class="btn about-btn abs" href="#">Read More <span class="arr"></span></a>
    <div class="about-frame abs"></div>
    <div class="about-dots abs"></div>
    <div class="about-photo abs" role="img" aria-label="Smiling students working together at a laptop"></div>
  </section>

  <!-- services -->
  <section class="services abs" role="img" aria-label="Dark background photo of a family embrace">
    <h2 class="section-title abs">OUR SERVICES</h2>
    <svg class="svc-map abs" width="1200" height="622" viewBox="0 0 1200 622" fill="none">
      <circle cx="600" cy="359" r="140" stroke="#8a8a8a" stroke-width="1.5"/>
      <g stroke="#cfcfcf" stroke-width="1.5">
        <polyline points="399,210 450,210 501,261"/>
        <polyline points="801,210 750,210 699,261"/>
        <line x1="399" y1="359" x2="460" y2="359"/>
        <line x1="801" y1="359" x2="740" y2="359"/>
        <polyline points="399,511 450,511 501,459"/>
        <polyline points="801,511 750,511 699,459"/>
      </g>
      <g fill="#e8232b" stroke="#fff" stroke-width="3">
        <circle cx="501" cy="261" r="6"/><circle cx="699" cy="261" r="6"/>
        <circle cx="460" cy="359" r="6"/><circle cx="740" cy="359" r="6"/>
        <circle cx="501" cy="459" r="6"/><circle cx="699" cy="459" r="6"/>
      </g>
      <g stroke="#fff" stroke-width="2">
        <circle cx="360" cy="210" r="38"/><circle cx="360" cy="359" r="38"/><circle cx="360" cy="511" r="38"/>
        <circle cx="838" cy="210" r="38"/><circle cx="838" cy="511" r="38"/>
      </g>
      <circle cx="838" cy="359" r="39" fill="#fff"/>
      <g fill="#fff">
        <circle cx="360" cy="198" r="7"/><path d="M346,224 q14,-20 28,0 z"/>
        <path d="M360,342 l14,6 v10 q0,14 -14,20 q-14,-6 -14,-20 v-10 z"/>
        <path d="M349,495 h16 l7,7 v25 h-23 z"/>
        <circle cx="838" cy="210" r="12"/>
        <path d="M822,508 q8,14 16,14 q8,0 16,-14 v12 q-8,12 -16,12 q-8,0 -16,-12 z"/><circle cx="838" cy="500" r="6"/>
      </g>
      <g fill="#111"><circle cx="360" cy="359" r="4"/><rect x="353" y="505" width="14" height="2"/><rect x="353" y="511" width="14" height="2"/><rect x="353" y="517" width="10" height="2"/><circle cx="838" cy="210" r="5"/></g>
      <path d="M838,370 q-14,-10 -10,-18 q5,-8 10,0 q5,-8 10,0 q4,8 -10,18 z" stroke="#e8232b" stroke-width="2.5" fill="none"/>
    </svg>
    <div class="svc-text l abs" style="top:185px">Lorem ipsum dolor sit amet consectetur adipisea</div>
    <div class="svc-text l abs" style="top:333px">Lorem ipsum dolor sit amet consectetur adipisea</div>
    <div class="svc-text l abs" style="top:484px">Lorem ipsum dolor sit amet consectetur adipisea</div>
    <div class="svc-text r abs" style="top:185px">Lorem ipsum dolor sit amet consectetur adipisea</div>
    <div class="svc-text r abs" style="top:333px">Lorem ipsum dolor sit amet consectetur adipisea</div>
    <div class="svc-text r abs" style="top:484px">Lorem ipsum dolor sit amet consectetur adipisea</div>
    <div class="svc-hub abs">guardnest</div>
  </section>

  <!-- articles -->
  <section class="articles">
    <h2 class="section-title abs">LATEST ARTICLES</h2>
    <article class="art-card abs" style="left:112px;top:2265px">
      <div class="img" role="img" aria-label="Happy family of four smiling together" style="background:linear-gradient(135deg,#6f8fa8,#e0b58a 50%,#d9c04a)"></div>
      <div class="box"><h3>Lorem ipsum dolor sit consec tetur</h3><p>Lorem ipsum dolor sit amet cons ecte tur adipiscing elit sedea do eiusmod tempor.</p></div>
    </article>
    <article class="art-card abs" style="left:398px;top:2265px">
      <div class="img" role="img" aria-label="Young girl hugging a parent at home" style="background:linear-gradient(135deg,#c9c3bb,#9aa6b3 50%,#e6ddd3)"></div>
      <div class="box"><h3>Lorem ipsum dolor sit consec tetur</h3><p>Lorem ipsum dolor sit amet cons ecte tur adipiscing elit sedea do eiusmod tempor.</p></div>
    </article>
    <article class="art-item abs" style="top:2265px">
      <div class="img" role="img" aria-label="Students studying around a laptop" style="background:linear-gradient(135deg,#8fa3b5,#d8cfc2,#5b6d82)"></div>
      <div class="txt"><h3>Lorem ipsum dolor sit a consec tetur</h3><p>Lorem ipsum dolor sit amet consecte tur adipiscing elit sedea.</p></div>
    </article>
    <article class="art-item abs" style="top:2396px">
      <div class="img" role="img" aria-label="Group of cheerful friends outdoors" style="background:linear-gradient(135deg,#a58a5e,#c24a3e,#3f4a3a)"></div>
      <div class="txt"><h3>Lorem ipsum dolor sit a consec tetur</h3><p>Lorem ipsum dolor sit amet consecte tur adipiscing elit sedea.</p></div>
    </article>
    <article class="art-item abs" style="top:2526px">
      <div class="img" role="img" aria-label="Students working together at a table" style="background:linear-gradient(135deg,#6d6a66,#c7b49a,#3b3a3c)"></div>
      <div class="txt"><h3>Lorem ipsum dolor sit a consec tetur</h3><p>Lorem ipsum dolor sit amet consecte tur adipiscing elit sedea.</p></div>
    </article>
  </section>

  <!-- contact -->
  <section class="contact abs" role="img" aria-label="Red tinted photo of a student writing">
    <h2 class="section-title abs">GET IN TOUCH</h2>
    <div class="field abs" style="left:166px;top:149px;width:283px;height:48px">Full Name</div>
    <div class="field abs" style="left:458px;top:149px;width:284px;height:48px">Phone Number</div>
    <div class="field abs" style="left:751px;top:149px;width:283px;height:48px">Email Address</div>
    <div class="field msg abs" style="left:166px;top:208px;width:868px;height:94px">Message...!</div>
    <div class="send abs">SEND MESSAGE</div>
  </section>

  <!-- footer -->
  <footer>
    <svg class="footer-shape abs" width="1200" height="386" viewBox="0 0 1200 386">
      <path d="M0,180 Q600,-110 1200,180 L1200,386 L0,386 Z" fill="#fff"/>
      <path d="M0,206 Q600,-70 1200,206 L1200,386 L0,386 Z" fill="#0b0b0b"/>
    </svg>
    <div class="footer-brand abs"><span class="dot"></span>guardnest.ca</div>
    <nav class="footer-nav abs">
      <span>HOME</span><span class="sep">|</span><span>ABOUT US</span><span class="sep">|</span><span>SERVICES</span><span class="sep">|</span><span>RESOURCES</span><span class="sep">|</span><span>CONTACT US</span>
    </nav>
    <div class="footer-contact abs">
      <span><svg class="ic" width="14" height="14" viewBox="0 0 24 24"><path fill="#e8232b" d="M6.6 10.8a15 15 0 0 0 6.6 6.6l2.2-2.2a1 1 0 0 1 1-.25 11.4 11.4 0 0 0 3.6.57 1 1 0 0 1 1 1V20a1 1 0 0 1-1 1A17 17 0 0 1 3 4a1 1 0 0 1 1-1h3.5a1 1 0 0 1 1 1c0 1.25.2 2.45.57 3.570a1 1 0 0 1-.25 1z"/></svg>+1 (555) 010 2040</span>
      <span>|</span>
      <span><svg class="ic" width="16" height="12" viewBox="0 0 16 12"><rect width="16" height="12" rx="1.5" fill="#e8232b"/><path d="M1,1 L8,7 L15,1" stroke="#fff" stroke-width="1.5" fill="none"/></svg>hello@guardnest.ca</span>
    </div>
    <div class="footer-social abs"><span class="on"></span><span></span><span></span></div>
    <div class="footer-rule abs"></div>
    <div class="copyright abs">© 2023 <b>guardnest.ca</b> &nbsp;|&nbsp; All Rights Reserved</div>
  </footer>

</div>
</body>
</html>
```